Business Cards for company that supports physicians that do medical research

Need to create a business card for Qorvel Studies (www.qorvelstudies.example), a company devoted to supporting physicians who conduct medical research. The form of the card should match the message of research and information quest. I have provided the logo of the company as an uploaded file. Designs should be simple and slick aimed at very high end clients.

Target Market(s)

Medical doctors that are also researchers

Industry/Entity Type

Medical

Contact Information for Business Card

Should feature logo and fields for personal info:
Name/title
Phone /email

Font styles to use
Serif
Sans Serif

Requirements
Must have
• Qorvel logo and fields for personal info:
• Name: Bertrand Okonfu
• Title: VP Research and Senior Analyst
• Phone: 555-203-4719
• email: info@qorvelstudies.example
Nice to have
• Interesting cards that I've seen:
• 1- all black/charcoal or very dark background
• 2- Plastic - semi-transparent
• 3- non-standard height-width ratios
• 4- Functional cards -- USB drive incorporated
Should not have
• Too busy; needs to stay very simple

```html
<!DOCTYPE html>
<html lang="en">
<head>
<meta charset="utf-8">
<title>Qorvel Studies — Business Cards</title>
<link href="https://fonts.googleapis.com/css2?family=Open+Sans:wght@400;600;700&display=swap" rel="stylesheet">
<style>
  :root {
    --backdrop: #e4e5e7;
    --card-green: #5bbd4a;
    --card-green-light: #6cc75a;
    --paper: #ffffff;
    --ink-grey: #5e5e60;
    --logo-green: #4aae3c;
    --text-light: #ffffff;
  }
  * { margin: 0; padding: 0; box-sizing: border-box; }
  html, body {
    width: 1200px; height: 900px; overflow: hidden;
    background: var(--backdrop);
    font-family: "Open Sans", Arial, sans-serif;
  }
  .sheet { position: relative; width: 1200px; height: 900px; }
  .card {
    position: absolute; left: 250px; width: 700px; height: 400px;
    border-radius: 4px; overflow: hidden;
    box-shadow: 0 6px 18px rgba(0,0,0,.18);
  }
  .card--back {
    top: 40px;
    background: radial-gradient(ellipse at 40% 40%, var(--card-green-light), var(--card-green) 70%);
    display: flex; align-items: center; justify-content: center;
  }
  .card--front { top: 465px; background: var(--paper); }
  .card__field { position: absolute; inset: 0; }
  .wordmark { font-weight: 600; letter-spacing: 1px; white-space: nowrap; }
  .card--back .wordmark { font-size: 50px; color: var(--ink-grey); }
  .card--front .wordmark {
    position: absolute; left: 36px; top: 172px;
    font-size: 34px; color: var(--logo-green);
  }
  .identity {
    position: absolute; right: 32px; top: 38px; text-align: right;
    color: var(--text-light);
  }
  .identity__name { font-size: 22px; font-weight: 700; }
  .identity__title { font-size: 15px; font-weight: 400; margin-top: 2px; }
  .contact {
    position: absolute; right: 32px; bottom: 42px; text-align: right;
    color: var(--text-light); font-size: 17px; line-height: 1.55;
    list-style: none;
  }
  .contact li { display: flex; justify-content: flex-end; align-items: center; gap: 8px; }
  .contact svg { width: 14px; height: 14px; fill: var(--text-light); }
</style>
</head>
<body>
<main class="sheet">

  <section class="card card--back" aria-label="Card back">
    <span class="wordmark">Qorvel Studies</span>
  </section>

  <section class="card card--front" aria-label="Card front">
    <svg class="card__field" viewBox="0 0 700 400" aria-hidden="true">
      <path d="M420 0 L700 0 L700 400 L280 400 Z" fill="var(--card-green)"/>
    </svg>

    <span class="wordmark">Qorvel Studies</span>

    <div class="identity">
      <p class="identity__name">Bertrand Okonfu</p>
      <p class="identity__title">VP Research and Senior Analyst</p>
    </div>

    <ul class="contact">
      <li>555-203-4719
        <svg viewBox="0 0 16 16" aria-hidden="true"><path d="M2 5 Q8 1 14 5 L12 7 L10 5.5 L6 5.5 L4 7 Z M4 8 H12 L13 14 H3 Z"/></svg>
      </li>
      <li>info@qorvelstudies.example
        <svg viewBox="0 0 16 16" aria-hidden="true"><path d="M1 3 H15 V13 H1 Z M2 4 L8 9 L14 4 Z" fill-rule="evenodd"/></svg>
      </li>
    </ul>
  </section>

</main>
</body>
</html>
```